The most modern business card ever !!!

Our company call “Vendalo”. Vendalo is a technology company specialized in cruises solutions. Out main product is a platform to reserve cruises. This is a revolutionary platform that make easier to travel agencies and final users to reserve cruises across dozen companies like tibba, wernu, hpv, dgb, etc..We are a “start up”, with a young team of developers and we want to transmit it.. For it, we want something different, a modern business card that represent cruises and technology.. When someone receive this card, this person should say: wowww this is different… this is modern… this is a cruise related company..
- diferent, modern
- traditions business card

```html
<!DOCTYPE html>
<html lang="en">
<head>
<meta charset="utf-8">
<title>Vendalo Business Card</title>
<link href="https://fonts.googleapis.com/css2?family=Oswald:wght@600&family=Work+Sans:wght@400;500&display=swap" rel="stylesheet">
<style>
  :root {
    --backdrop: #121212;
    --card-dark: #1c1c1c;
    --card-light: #2a2a2a;
    --card-edge: #2f2f2f;
    --gloss: #4a4a4a;
    --gloss-soft: #5e5e5e;
    --gloss-highlight: rgba(255, 255, 255, 0.08);
    --ink-light: #d9d9d9;
    --rule: #4a4a4a;
  }
  * { margin: 0; padding: 0; box-sizing: border-box; }
  html, body {
    width: 1200px;
    height: 900px;
    overflow: hidden;
    background: var(--backdrop);
  }
  .canvas {
    position: relative;
    width: 1200px;
    height: 900px;
    background: radial-gradient(ellipse at 60% 45%, #1d1d1d 0%, var(--backdrop) 70%);
  }
  .card {
    position: absolute;
    left: 290px;
    width: 620px;
    height: 354px;
    background: linear-gradient(135deg, var(--card-dark) 0%, var(--card-light) 60%, var(--card-dark) 100%);
    border: 1px solid var(--card-edge);
    box-shadow: 0 18px 40px rgba(0, 0, 0, 0.55);
  }
  .card--front { top: 56px; }
  .card--back { top: 450px; }

  .brand-name {
    position: absolute;
    inset: 0;
    display: flex;
    align-items: center;
    justify-content: center;
    font-family: "Work Sans", sans-serif;
    font-weight: 500;
    font-size: 72px;
    letter-spacing: 1px;
    color: var(--ink-light);
  }

  .identity {
    position: absolute;
    left: 30px;
    top: 116px;
    width: 260px;
    text-align: right;
  }
  .identity__name {
    font-family: "Oswald", sans-serif;
    font-weight: 600;
    font-size: 36px;
    line-height: 1;
    letter-spacing: 1px;
    color: var(--gloss);
    text-transform: uppercase;
    text-shadow: 0 1px 0 var(--gloss-highlight);
  }
  .identity__role {
    margin-top: 6px;
    font-family: "Work Sans", sans-serif;
    font-size: 15px;
    letter-spacing: 1.5px;
    color: var(--gloss-soft);
  }
  .divider {
    position: absolute;
    left: 310px;
    top: 114px;
    width: 1px;
    height: 80px;
    background: var(--rule);
  }
  .contacts {
    position: absolute;
    left: 330px;
    top: 118px;
    list-style: none;
    font-family: "Work Sans", sans-serif;
    font-size: 17px;
    letter-spacing: 1.5px;
    color: var(--ink-light);
  }
  .contacts__item {
    display: flex;
    align-items: center;
    gap: 9px;
    height: 25px;
  }
  .contacts__icon {
    width: 12px;
    height: 12px;
    flex: none;
  }
  .address {
    position: absolute;
    left: 40px;
    bottom: 44px;
    font-family: "Work Sans", sans-serif;
    font-weight: 500;
    font-size: 16px;
    letter-spacing: 2px;
    color: var(--gloss);
    text-shadow: 0 1px 0 var(--gloss-highlight);
  }
</style>
</head>
<body>
<main class="canvas">
  <section class="card card--front">
    <div class="brand-name">Vendalo</div>
  </section>

  <section class="card card--back">
    <div class="identity">
      <p class="identity__name">Daniel Reyes</p>
      <p class="identity__role">Director</p>
    </div>
    <div class="divider"></div>
    <ul class="contacts">
      <li class="contacts__item">
        <svg class="contacts__icon" viewBox="0 0 12 12" aria-hidden="true">
          <path d="M3 1 L5 3.5 L4 5 Q5 7.5 7 8 L8.5 7 L11 9 L9.5 11 Q3.5 10.5 1 3 Z" fill="var(--ink-light)"/>
        </svg>
        <span>(555) 203-4187</span>
      </li>
      <li class="contacts__item">
        <svg class="contacts__icon" viewBox="0 0 12 12" aria-hidden="true">
          <rect x="1" y="2.5" width="10" height="7" fill="none" stroke="var(--ink-light)" stroke-width="1.2"/>
          <path d="M1 2.5 L6 6.5 L11 2.5" fill="none" stroke="var(--ink-light)" stroke-width="1.2"/>
        </svg>
        <span>info@vendalo.com.br</span>
      </li>
      <li class="contacts__item">
        <svg class="contacts__icon" viewBox="0 0 12 12" aria-hidden="true">
          <circle cx="6" cy="6" r="5" fill="none" stroke="var(--ink-light)" stroke-width="1.1"/>
          <ellipse cx="6" cy="6" rx="2.2" ry="5" fill="none" stroke="var(--ink-light)" stroke-width="1"/>
          <path d="M1 6 H11" stroke="var(--ink-light)" stroke-width="1"/>
        </svg>
        <span>www.vendalo.com.br</span>
      </li>
    </ul>
    <p class="address">48b Harbour Lane, Port Meridian, 4021</p>
  </section>
</main>
</body>
</html>
```